K7 Electrical Services Ltd Web design

I require a web site for my new electrical contracting company. We are customer service orientated. Offering high value electrical installations, design and maintenance. Focused on custom residential and commercial upgrading. Lighting design and application are paramount in our company's services. Industry leading product use and integration are always on the forefront with our customer client services. As well as energy efficiency.

Target Market(s)

Homebuilders, General Contractors, Property management companies, clients, individuals,

Industry/Entity Type

Electric Company

Coding

Coded - Design and coding required

Number of Pages Required

3 page

Requirements
Must have
• Classic, modern, edgy but not trendy . Appeals to the masse.
• 3 page
• home page
• about page
• gallery page
• ability to contact from the webiste
Nice to have
• open to all types of designs that are relative to the construction industry.
• Black, Grey, metallic ice blue and deep purple colours from the logo.
Should not have
• anything cheesy with cartoon light bulb images.

```html
<!DOCTYPE html>
<html lang="en">
<head>
<meta charset="utf-8">
<title>K7 Electrical Services Ltd</title>
<link href="https://fonts.googleapis.com/css2?family=ABeeZee&family=Open+Sans:wght@400;600&display=swap" rel="stylesheet">
<style>
:root{
  --purple:#5c2a8a;
  --purple-dark:#4b2172;
  --charcoal:#333333;
  --footer:#2e2e2e;
  --grey-band:#ededed;
  --heading:#555555;
  --body:#666666;
  --white:#ffffff;
}
*{box-sizing:border-box;margin:0;padding:0}
html,body{width:1200px;height:3066px;overflow:hidden}
body{font-family:'Open Sans',Arial,sans-serif;color:var(--body);background:var(--white)}
.page{position:relative;width:1200px;height:3066px}

.hero{position:relative;height:647px;background:linear-gradient(135deg,#e9e6ea 0%,#f6f6f7 35%,#eef1f5 60%,#dfe6ee 100%);display:flex;align-items:center;justify-content:center}
.brand-name{font-family:'ABeeZee',Arial,sans-serif;color:#5e5e60;font-size:96px;line-height:1.1;text-align:center;letter-spacing:2px;text-transform:uppercase}

.main-nav{height:51px;background:var(--purple);position:relative}
.main-nav ul{list-style:none;display:flex;position:absolute;left:78px;top:0;height:51px}
.main-nav li{height:51px;display:flex;align-items:center;padding:0 20px;font-size:17px;color:var(--white);text-transform:uppercase}
.main-nav li.current{background:var(--charcoal);padding:0 31px}
.quote-btn{position:absolute;right:78px;top:0;width:176px;height:51px;background:var(--charcoal);color:var(--white);font-weight:600;font-size:20px;display:flex;align-items:center;justify-content:center;text-transform:uppercase}

.section-title{font-family:'ABeeZee',Arial,sans-serif;font-size:40px;color:var(--heading);text-align:center;font-weight:400}
.rule{width:40px;height:3px;background:var(--purple);margin:14px auto 0}
.lead{font-size:15px;line-height:28px;text-align:center;width:790px;margin:0 auto}

.services{height:637px;padding-top:48px}
.services .lead{margin-top:20px}
.service-grid{display:flex;justify-content:space-between;width:1044px;margin:38px auto 0}
.service{width:322px;text-align:center}
.service .photo{height:198px}
.service h3{font-family:'ABeeZee',Arial,sans-serif;font-weight:400;font-size:23px;color:#444;margin-top:22px}
.service p{font-size:15px;line-height:25px;margin-top:6px}
.ph-pliers{background:linear-gradient(135deg,#c9b8a8,#d98a4a 45%,#8c7a6c)}
.ph-design{background:linear-gradient(135deg,#f2f2f2,#dfe3e8 60%,#f0b070)}
.ph-maint{background:linear-gradient(135deg,#7fa4c8,#c6c2bc 50%,#6e7278)}

.welcome{height:417px;background:var(--grey-band);padding-top:48px}
.welcome .lead{width:800px;margin-top:26px}
.welcome .lead + .lead{margin-top:4px}
.read-more{display:block;width:186px;height:47px;margin:24px auto 0;border-radius:24px;background:var(--purple);color:var(--white);font-weight:600;font-size:19px;text-align:center;line-height:47px;text-transform:uppercase}

.projects{height:636px;background:linear-gradient(160deg,#2b2b2d,#1d1c1e 50%,#3a2f2a);padding-top:38px}
.projects .section-title{color:var(--white)}
.projects .rule{background:#8a8a8a}
.project-grid{display:grid;grid-template-columns:repeat(3,333px);grid-auto-rows:210px;column-gap:22px;row-gap:21px;width:1044px;margin:33px auto 0}
.pj-1{background:linear-gradient(135deg,#7a96c4,#3f5e8e 50%,#a8a39a)}
.pj-2{background:linear-gradient(135deg,#e8d3a8,#b8915a 50%,#6c5034)}
.pj-3{background:linear-gradient(135deg,#d4a56a,#9a6a3a 50%,#e2c294)}
.pj-4{background:linear-gradient(135deg,#e0ece4,#4a9a5e 50%,#efefef)}
.pj-5{background:linear-gradient(135deg,#d8e2ee,#f4f6f8 50%,#9fa8b4)}
.pj-6{background:linear-gradient(135deg,#c8b8a0,#6a5848 50%,#e8dcc8)}

.testimonials{position:relative;height:427px;padding-top:44px}
.quote-mark{display:block;margin:40px auto 0}
.testimonials .lead{margin-top:10px;width:800px}
.client{text-align:center;font-size:16px;color:#444;margin-top:10px}
.slider-arrow{position:absolute;top:252px;width:41px;height:33px}
.slider-arrow.prev{left:78px}
.slider-arrow.next{right:78px}

.site-footer{height:196px;background:var(--footer);text-align:center;padding-top:52px}
.footer-brand{font-family:'ABeeZee',Arial,sans-serif;color:var(--white);font-size:34px;letter-spacing:2px;text-transform:uppercase}
.footer-nav{list-style:none;display:flex;justify-content:center;gap:60px;margin-top:40px;font-size:15px;color:var(--white)}
.copyright{height:55px;background:var(--purple);color:#e8e0f0;font-size:15px;text-align:center;line-height:55px}
</style>
</head>
<body>
<div class="page">
  <header class="hero" role="img" aria-label="Soft background photo of hands stripping electrical wires with pliers">
    <div class="brand-name">K7 Electrical<br>Services</div>
  </header>

  <nav class="main-nav">
    <ul>
      <li class="current">Home</li>
      <li>About Us</li>
      <li>Gallery</li>
      <li>Contact Us</li>
    </ul>
    <div class="quote-btn">Get a Quote</div>
  </nav>

  <section class="services">
    <h2 class="section-title">Our Services</h2>
    <div class="rule"></div>
    <p class="lead">Lorem Ipsum is simply dummy text of the printing and typesetting industry. Lorem Ipsum has been the industry's standard dummy text ever since the 1500s, when an unknown printer took a galley</p>
    <div class="service-grid">
      <article class="service">
        <div class="photo ph-pliers" role="img" aria-label="Photo of pliers cutting an electrical wire"></div>
        <h3>Electrical installations</h3>
        <p>Lorem Ipsum is simply dummy text of the printing and typesetting industry. Lorem Ipsum has been the industry's standard.</p>
      </article>
      <article class="service">
        <div class="photo ph-design" role="img" aria-label="Photo of an electrical wiring plan with a pencil"></div>
        <h3>Design</h3>
        <p>Lorem Ipsum is simply dummy text of the printing and typesetting industry. Lorem Ipsum has been the industry's standard.</p>
      </article>
      <article class="service">
        <div class="photo ph-maint" role="img" aria-label="Photo of an electrician working on a distribution board"></div>
        <h3>Maintenance</h3>
        <p>Lorem Ipsum is simply dummy text of the printing and typesetting industry. Lorem Ipsum has been the industry's standard.</p>
      </article>
    </div>
  </section>

  <section class="welcome">
    <h2 class="section-title">Welcome to K7 Electrical Services</h2>
    <div class="rule"></div>
    <p class="lead">Lorem Ipsum is simply dummy text of the printing and typesetting industry. Lorem Ipsum has been the industry's standard dummy text ever since the 1500s, when an unknown printer took a galley of type and scrambled it to make a type specimen book. It has survived not only five centuries, but also the leap.</p>
    <p class="lead">Lorem Ipsum is simply dummy text of the printing and typesetting industry. Lorem Ipsum has been the industry's standard dummy text ever since the 1500s, when an unknown printer took a galley of type.</p>
    <span class="read-more">Read More</span>
  </section>

  <section class="projects" role="group" aria-label="Latest projects over a dark photo of cabling">
    <h2 class="section-title">Latest Projects</h2>
    <div class="rule"></div>
    <div class="project-grid">
      <div class="pj-1" role="img" aria-label="Photo of a lit industrial warehouse"></div>
      <div class="pj-2" role="img" aria-label="Photo of a kitchen with warm lighting"></div>
      <div class="pj-3" role="img" aria-label="Photo of a timber-framed room during wiring"></div>
      <div class="pj-4" role="img" aria-label="Photo of a modern office interior"></div>
      <div class="pj-5" role="img" aria-label="Photo of a bright empty commercial hall"></div>
      <div class="pj-6" role="img" aria-label="Photo of a living room with feature lighting"></div>
    </div>
  </section>

  <section class="testimonials">
    <h2 class="section-title">Testimonials</h2>
    <div class="rule"></div>
    <svg class="quote-mark" width="74" height="74" viewBox="0 0 74 74" aria-hidden="true">
      <circle cx="37" cy="37" r="37" fill="#5c2a8a"/>
      <path d="M22 44v-8c0-6 4-10 9-11v4c-3 1-4 3-4 6h4v9z M40 44v-8c0-6 4-10 9-11v4c-3 1-4 3-4 6h4v9z" fill="#fff"/>
    </svg>
    <p class="lead">Lorem Ipsum is simply dummy text of the printing and typesetting industry. Lorem Ipsum has been the industry's standard dummy text ever since the 1500s, when an unknown printer took a galley of type and scrambled it to make a type specimen book. It has survived not only five centuries, but also the leap.</p>
    <p class="client">-Client Name</p>
    <svg class="slider-arrow prev" viewBox="0 0 41 33" aria-label="Previous">
      <rect width="41" height="33" fill="#5c2a8a"/>
      <path d="M29 16.5H12M18 10l-6 6.5 6 6.5" stroke="#fff" stroke-width="2" fill="none"/>
    </svg>
    <svg class="slider-arrow next" viewBox="0 0 41 33" aria-label="Next">
      <rect width="41" height="33" fill="#5c2a8a"/>
      <path d="M12 16.5h17M23 10l6 6.5-6 6.5" stroke="#fff" stroke-width="2" fill="none"/>
    </svg>
  </section>

  <footer class="site-footer">
    <div class="footer-brand">K7 Electrical Services</div>
    <ul class="footer-nav">
      <li>Home</li>
      <li>About Us</li>
      <li>Gallery</li>
      <li>Contact Us</li>
    </ul>
  </footer>
  <div class="copyright">©K7 ELECTRICAL - 2018. All Rights Reserved.</div>
</div>
</body>
</html>
```